Automotive Accessories Business Card

Design a business template that match our new logo design and our industry.

https://www.qelmotorgear.com/

Target Market(s)

Aftermarket auto parts and accessories

Industry/Entity Type

automotive

Contact Information for Business Card

company logo

Font styles to use
Serif
Sans Serif

Colors
EB3D1F
EC4F4E
F09395
F8D3D4
FCEDEE

```html
<!DOCTYPE html>
<html lang="en">
<head>
<meta charset="utf-8">
<title>QEL Motor Gear – Business Card</title>
<link rel="stylesheet" href="https://fonts.googleapis.com/css2?family=Montserrat:wght@400;500;700&display=swap">
<style>
  :root {
    --backdrop: #c9c9c9;
    --card-white: #ffffff;
    --card-dark: #3f3f41;
    --brand-red: #d9232d;
    --ink: #3a3a3c;
    --ink-soft: #555557;
    --divider: #9a9a9a;
    --back-mark: #2f2f31;
  }
  * { box-sizing: border-box; margin: 0; padding: 0; }
  html, body { width: 1200px; height: 788px; overflow: hidden; }
  body {
    background: var(--backdrop);
    font-family: "Montserrat", sans-serif;
    position: relative;
  }
  .card {
    position: absolute;
    width: 525px;
    height: 300px;
    border-radius: 4px;
    box-shadow: 0 10px 24px rgba(0,0,0,0.22);
  }
  .card--front { left: 50px; top: 120px; background: var(--card-white); }
  .card--back  { left: 625px; top: 368px; background: var(--card-dark);
                 display: flex; align-items: center; justify-content: center; }

  .brand {
    position: absolute;
    left: 150px; top: 50px;
    display: flex; align-items: center; gap: 12px;
  }
  .brand__square { width: 22px; height: 22px; background: var(--brand-red); }
  .brand__name {
    font-weight: 700; font-size: 28px; color: var(--ink);
    letter-spacing: 0.5px; white-space: nowrap;
  }

  .person { position: absolute; left: 40px; top: 150px; text-align: right; width: 200px; }
  .person__name { color: var(--brand-red); font-weight: 700; font-size: 20px; letter-spacing: 0.5px; }
  .person__title { color: var(--ink-soft); font-size: 13px; margin-top: 2px; }

  .divider { position: absolute; left: 262px; top: 138px; width: 1px; height: 62px; background: var(--divider); }

  .contact { position: absolute; left: 282px; top: 136px; list-style: none; }
  .contact li {
    display: flex; align-items: center; gap: 7px;
    font-size: 13px; color: var(--ink); line-height: 22px;
  }
  .contact svg { width: 11px; height: 11px; flex: none; }

  .address { position: absolute; left: 0; right: 0; top: 238px; text-align: center; font-size: 13px; color: var(--ink); }

  .back-brand { display: flex; align-items: center; gap: 16px; }
  .back-brand__square { width: 34px; height: 34px; background: var(--back-mark); }
  .back-brand__name { font-weight: 700; font-size: 38px; color: var(--back-mark); white-space: nowrap; }
</style>
</head>
<body>
  <section class="card card--front">
    <div class="brand">
      <span class="brand__square"></span>
      <span class="brand__name">QEL Motor Gear Inc</span>
    </div>

    <div class="person">
      <p class="person__name">DANIEL MERCER</p>
      <p class="person__title">CEO/Founder</p>
    </div>

    <span class="divider"></span>

    <ul class="contact">
      <li>
        <svg viewBox="0 0 12 12"><path fill="#d9232d" d="M2.5 1 L4.5 1 L5.2 3.5 L4 4.5 Q5 6.8 7.5 8 L8.5 6.8 L11 7.5 L11 9.5 Q10.5 11 9 11 Q1 10 1 3 Q1 1.5 2.5 1Z"/></svg>
        1-866-555-0148
      </li>
      <li>
        <svg viewBox="0 0 12 12"><rect x="0.5" y="2" width="11" height="8" rx="1" fill="#d9232d"/><path d="M1 2.8 L6 6.5 L11 2.8" stroke="#fff" stroke-width="1" fill="none"/></svg>
        sales@qelmotorgear.com
      </li>
      <li>
        <svg viewBox="0 0 12 12"><circle cx="6" cy="6" r="5.5" fill="#d9232d"/><path d="M0.5 6 H11.5 M6 0.5 V11.5 M2 3 Q6 4.5 10 3 M2 9 Q6 7.5 10 9" stroke="#fff" stroke-width="0.7" fill="none"/></svg>
        www.qelmotorgear.com
      </li>
    </ul>

    <p class="address">418 W. Cedar Ave. Unit C Linden, CA, 91820</p>
  </section>

  <section class="card card--back">
    <div class="back-brand">
      <span class="back-brand__square"></span>
      <span class="back-brand__name">QEL Motor Gear Inc</span>
    </div>
  </section>
</body>
</html>
```